I'm looking for a smart new design for business cards

Industry/Entity Type

Commercial Electrical

Contact Information for Business Card

Logo, name, email, position, website QR

Requirements
Nice to have
• Logo embedded behind the text side

```html
<!DOCTYPE html>
<html lang="en">
<head>
<meta charset="utf-8">
<title>Brightwire Commercial Electrical – Business Card</title>
<link rel="stylesheet" href="https://fonts.googleapis.com/css2?family=Montserrat:wght@400;500;700;800&display=swap">
<style>
  :root {
    --stage: #979797;
    --navy: #2b2a74;
    --red: #d91f2c;
    --white: #ffffff;
    --ink: #1c1c1c;
    --text: #3a3a3a;
    --mist: #e6e5ef;
  }
  * { box-sizing: border-box; margin: 0; padding: 0; }
  html, body {
    width: 1200px; height: 1108px; overflow: hidden;
    background: var(--stage);
    font-family: "Montserrat", Arial, sans-serif;
  }
  .card {
    position: absolute; left: 242px;
    width: 715px; height: 408px;
    border-radius: 30px; overflow: hidden;
  }
  .card--front { top: 119px; background: var(--navy); }
  .card--back { top: 580px; background: var(--white); }

  .brand {
    position: absolute; left: 0; right: 0;
    display: flex; flex-direction: column; align-items: center;
  }
  .brand__mark {
    display: flex; align-items: center; gap: 18px;
  }
  .brand__square { width: 34px; height: 34px; background: var(--red); flex: none; }
  .brand__name {
    font-weight: 800; letter-spacing: 2px; line-height: 1; white-space: nowrap;
  }
  .brand__tagline {
    font-weight: 800; letter-spacing: 1px; text-align: center; line-height: 1.2; white-space: nowrap;
  }

  .card--front .brand { top: 100px; }
  .card--front .brand__name { font-size: 80px; color: var(--white); }
  .card--front .brand__tagline { margin-top: 60px; font-size: 30px; color: var(--white); }

  .map-area {
    position: absolute; left: 0; top: 0; width: 367px; height: 408px;
    background: var(--mist);
    clip-path: polygon(35% 0, 100% 100%, 0 100%, 0 57%);
  }

  .person { position: absolute; left: 34px; top: 34px; }
  .person__name { font-size: 32px; font-weight: 700; color: var(--red); line-height: 1.1; }
  .person__role { margin-top: 6px; font-size: 17px; font-weight: 500; color: var(--text); }

  .contact { position: absolute; left: 34px; list-style: none; }
  .contact--phones { top: 184px; }
  .contact--online { top: 318px; }
  .contact li {
    display: flex; align-items: center; gap: 8px;
    height: 28px; font-size: 18px; color: var(--text);
  }
  .contact svg { width: 16px; height: 16px; fill: var(--red); flex: none; }

  .card--back .brand { left: 290px; right: 24px; top: 150px; }
  .card--back .brand__mark { gap: 14px; }
  .card--back .brand__square { width: 28px; height: 28px; }
  .card--back .brand__name { font-size: 46px; letter-spacing: 1px; color: var(--navy); }
  .card--back .brand__tagline { margin-top: 64px; font-size: 23px; color: var(--ink); }
</style>
</head>
<body>

<section class="card card--front">
  <div class="brand">
    <div class="brand__mark">
      <span class="brand__square"></span>
      <span class="brand__name">BRIGHTWIRE</span>
    </div>
    <p class="brand__tagline">COMMERCIAL ELECTRICAL</p>
  </div>
</section>

<section class="card card--back">
  <div class="map-area" role="img" aria-label="Faint map of Australia in the background"></div>

  <div class="person">
    <h1 class="person__name">Daniel Harper</h1>
    <p class="person__role">Managing Director</p>
  </div>

  <ul class="contact contact--phones">
    <li>
      <svg viewBox="0 0 16 16" aria-hidden="true"><path d="M1 6c0-2 3-3 7-3s7 1 7 3v1h-3V5.5H4V7H1zM3 8h10l1 6H2zm5 1.5a2 2 0 1 0 0 4 2 2 0 0 0 0-4z"/></svg>
      123 456 789
    </li>
    <li>
      <svg viewBox="0 0 16 16" aria-hidden="true"><path d="M4 0h8a1 1 0 0 1 1 1v14a1 1 0 0 1-1 1H4a1 1 0 0 1-1-1V1a1 1 0 0 1 1-1zm1 2v10h6V2zm3 11a1 1 0 1 0 0 2 1 1 0 0 0 0-2z"/></svg>
      123 456 789
    </li>
  </ul>

  <ul class="contact contact--online">
    <li>
      <svg viewBox="0 0 16 16" aria-hidden="true"><path d="M1 3h14v10H1zm1.5 1.2L8 8.5l5.5-4.3z"/></svg>
      hello@brightwire.example
    </li>
    <li>
      <svg viewBox="0 0 16 16" aria-hidden="true"><circle cx="8" cy="8" r="7"/><path d="M1 8h14M8 1c-3 3-3 11 0 14M8 1c3 3 3 11 0 14" stroke="#fff" stroke-width="1" fill="none"/></svg>
      www.brightwire.example
    </li>
  </ul>

  <div class="brand">
    <div class="brand__mark">
      <span class="brand__square"></span>
      <span class="brand__name">BRIGHTWIRE</span>
    </div>
    <p class="brand__tagline">COMMERCIAL ELECTRICAL</p>
  </div>
</section>

</body>
</html>
```